Luxury Wine Label for New Startup Winery

We need a wine label for our new winery startup. We have worked with a local designer but do not feel the resulting label / logo have the elevation required to present our brand as a luxury wine. Our winery is called "Quailbrook Vineyards" and we are focused on extremely high quality hand crafted artisan and estate wines from the Pacific Northwest.
We would like to see designs that utilize a tree line, or other imagery that represents the "Quailbrook" part of our company name. Another interesting feature could be wood grain.
A logo will be required based on your design so please design with this in mind:
This logo should be consistent with the wine bottle label design, and should be representative of our high end exclusive wine while giving a sense of place (Oregon/ Pacific Northwest.)
I will supply an image of the design we received from our local designer, PLEASE NOTE: in general we do like wood grain and tree line concepts but feel the execution was poorly done.
ATTN: Logo design should be suitable for use on: Bottles (Red wine/rose/white wine), Bussiness cards, vehicle signage, business signage, etc
P.S.:
If you have a design that is not outside the box we are still interested in seeing it.
Label is for a burgundy style bottle with a label height of 3.5 - 4" and a width of 3.5-4"
any label <= 4"x4" and >=3.5"x3.5" will be acceptable:
HOWEVER Width should be greater than or equal to height due to the bottle format
Target Market(s)
Wine enthusiasts with adequate discretionary budgets to afford $100 bottles of wine.
Industry/Entity Type
Wine / Winery
Requirements
Must have
- A sense of luxury, a feel of exclusivity, and a theme consistent with our product and brand name
Nice to have
- Tree line, wood grain or other wood themes. Serif fonts
Should not have
- anything cheesy, off topic, hard to read script fonts or anything that makes the label hard to read from a few feet away or too busy

```html
<!DOCTYPE html>
<html lang="en">
<head>
<meta charset="utf-8">
<title>Quailbrook Vineyards – Wine Label</title>
<link rel="stylesheet" href="https://fonts.googleapis.com/css2?family=Big+Shoulders+Display:wght@500&family=Allura&family=Oswald:wght@400&display=swap">
<style>
  :root {
    --backdrop: #e9e9ec;
    --label-deep: #16171a;
    --label-mid: #2a2b30;
    --label-sheen: #3a3b41;
    --gold: #d9b45e;
    --gold-light: #f1d690;
    --gold-dark: #a47a32;
    --ink-soft: #cfc6b4;
  }
  * { margin: 0; padding: 0; box-sizing: border-box; }
  html, body {
    width: 1200px;
    height: 903px;
    overflow: hidden;
    background: var(--backdrop);
  }
  .canvas {
    position: relative;
    width: 1200px;
    height: 903px;
    display: flex;
    align-items: center;
    justify-content: center;
  }
  .wine-label {
    position: relative;
    width: 880px;
    height: 800px;
    overflow: hidden;
    box-shadow: 0 14px 40px rgba(0,0,0,0.25);
  }
  .label-texture {
    position: absolute;
    inset: 0;
    background:
      radial-gradient(ellipse 70% 40% at 30% 25%, var(--label-sheen) 0%, transparent 70%),
      radial-gradient(ellipse 60% 35% at 75% 70%, var(--label-sheen) 0%, transparent 70%),
      linear-gradient(160deg, var(--label-mid) 0%, var(--label-deep) 55%, var(--label-mid) 100%);
  }
  .label-lines {
    position: absolute;
    inset: 0;
  }
  .winery-name {
    position: absolute;
    top: 150px;
    left: 0;
    width: 100%;
    text-align: center;
    font-family: "Big Shoulders Display", "Oswald", sans-serif;
    font-weight: 500;
    font-size: 76px;
    line-height: 1;
    letter-spacing: 1px;
    color: var(--gold);
    transform: rotate(-2deg);
    white-space: nowrap;
  }
  .estate-vignette {
    position: absolute;
    top: 280px;
    left: 228px;
    width: 424px;
    height: 240px;
    border-radius: 50%;
    background: radial-gradient(ellipse at 50% 55%, var(--gold-dark) 0%, #5b4620 35%, var(--label-deep) 75%);
  }
  .tagline {
    position: absolute;
    left: 0;
    width: 100%;
    text-align: center;
    font-family: "Allura", cursive;
    font-size: 32px;
    line-height: 1.2;
    color: var(--gold-light);
    white-space: nowrap;
    transform: rotate(-3deg);
  }
  .tagline--top { top: 582px; }
  .tagline--bottom { top: 626px; }
  .volume-strength {
    position: absolute;
    top: 712px;
    left: 0;
    width: 100%;
    text-align: center;
    font-family: "Oswald", sans-serif;
    font-size: 16px;
    letter-spacing: 1px;
    color: var(--ink-soft);
  }
  .volume-strength .divider {
    display: inline-block;
    width: 1px;
    height: 18px;
    margin: 0 8px;
    vertical-align: middle;
    background: var(--ink-soft);
  }
</style>
</head>
<body>
<main class="canvas">
  <section class="wine-label">
    <div class="label-texture" role="img" aria-label="Dark charcoal flowing wood-grain wave pattern"></div>

    <svg class="label-lines" width="880" height="800" viewBox="0 0 880 800" aria-hidden="true">
      <defs>
        <linearGradient id="goldStroke" x1="0" x2="1" y1="0" y2="0">
          <stop offset="0" stop-color="#a47a32"/>
          <stop offset="0.5" stop-color="#f1d690"/>
          <stop offset="1" stop-color="#a47a32"/>
        </linearGradient>
      </defs>
      <path d="M0 48 Q180 34 360 44 Q500 52 600 28 Q650 14 680 0" fill="none" stroke="url(#goldStroke)" stroke-width="2.5"/>
      <path d="M668 0 Q710 34 880 44" fill="none" stroke="url(#goldStroke)" stroke-width="1.5"/>
      <path d="M0 416 Q110 400 220 400" fill="none" stroke="url(#goldStroke)" stroke-width="3"/>
      <path d="M660 400 Q770 400 880 416" fill="none" stroke="url(#goldStroke)" stroke-width="3"/>
      <ellipse cx="440" cy="400" rx="220" ry="128" fill="none" stroke="url(#goldStroke)" stroke-width="3"/>
      <ellipse cx="440" cy="400" rx="212" ry="120" fill="none" stroke="url(#goldStroke)" stroke-width="1.2"/>
      <path d="M0 782 Q220 752 440 758 Q660 764 880 738" fill="none" stroke="url(#goldStroke)" stroke-width="2.5"/>
    </svg>

    <div class="estate-vignette" role="img" aria-label="Gold engraved illustration of an estate with towers, vineyard rows, hills and grape vines"></div>

    <h1 class="winery-name">QUAILBROOK VINEYARDS</h1>

    <p class="tagline tagline--top">Premium Quality Hand Crafted</p>
    <p class="tagline tagline--bottom">Artisan and Estate Wines from the Pacific Northwest</p>

    <p class="volume-strength">700ML<span class="divider"></span>12,5 % ALCOHOL</p>
  </section>
</main>
</body>
</html>
```